Redesign of business card for Cedar Ridge Mechanical

We are looking for a new design for our business cards for Cedar Ridge Mechanical. We are a plumbing & HVAC construction company, operating on the West Coast of Canada and USA. Logo attached.
Industry/Entity Type
Construction - Plumbing & HVAC
Contact Information for Business Card
Name, address, phone numbers, email, website address
Look and feel
Each slider illustrates characteristics of the customer's brand and the style your logo design should communicate.

```html
<!DOCTYPE html>
<html lang="en">
<head>
<meta charset="utf-8">
<title>Cedar Ridge Mechanical – Business Card</title>
<link rel="stylesheet" href="https://fonts.googleapis.com/css2?family=Montserrat:wght@400;700&display=swap">
<style>
  :root {
    --stage: #3a3a3a;
    --card-black: #141414;
    --mark-gloss: #262626;
    --card-white: #ffffff;
    --ink: #0d0d0d;
    --ink-soft: #2a2a2a;
    --band-text: #ffffff;
  }
  html, body {
    margin: 0;
    padding: 0;
    width: 1200px;
    height: 689px;
    overflow: hidden;
    background: var(--stage);
    font-family: "Montserrat", sans-serif;
  }
  .canvas {
    position: relative;
    width: 1200px;
    height: 689px;
    display: flex;
    align-items: center;
    justify-content: center;
    gap: 50px;
  }
  .card {
    position: relative;
    width: 520px;
    height: 298px;
    border-radius: 22px;
    overflow: hidden;
    box-shadow: 0 14px 34px rgba(0,0,0,.45);
  }

  /* Front */
  .card--front {
    background: var(--card-black);
    display: flex;
    align-items: center;
    justify-content: center;
  }
  .brand {
    display: flex;
    align-items: center;
    gap: 14px;
  }
  .brand__square {
    width: 26px;
    height: 26px;
    background: currentColor;
  }
  .brand__name {
    font-weight: 700;
    text-transform: uppercase;
    letter-spacing: 1px;
  }
  .card--front .brand { color: var(--mark-gloss); }
  .card--front .brand__name { font-size: 26px; }

  /* Back */
  .card--back {
    background: var(--card-white);
    color: var(--ink);
  }
  .back__brand {
    position: absolute;
    left: 34px;
    top: 100px;
    width: 200px;
    color: var(--ink);
  }
  .back__brand .brand { gap: 10px; }
  .back__brand .brand__square { width: 18px; height: 18px; flex: none; }
  .back__brand .brand__name { font-size: 15px; line-height: 1.25; }
  .divider {
    position: absolute;
    left: 252px;
    top: 48px;
    width: 1.5px;
    height: 150px;
    background: var(--ink);
  }
  .contact {
    position: absolute;
    left: 276px;
    top: 42px;
  }
  .contact__name {
    margin: 0;
    font-size: 22px;
    font-weight: 700;
    letter-spacing: .5px;
  }
  .contact__role {
    margin: 2px 0 18px;
    font-size: 14px;
    color: var(--ink-soft);
  }
  .contact__list {
    list-style: none;
    margin: 0;
    padding: 0;
    font-size: 14px;
    line-height: 24px;
  }
  .contact__list li {
    display: flex;
    align-items: center;
    gap: 8px;
  }
  .contact__list svg { width: 12px; height: 12px; fill: var(--ink); flex: none; }
  .band {
    position: absolute;
    left: 0;
    right: 0;
    top: 222px;
    height: 34px;
    background: var(--ink);
    color: var(--band-text);
    font-size: 14px;
    display: flex;
    align-items: center;
    justify-content: flex-end;
    padding-right: 40px;
  }
</style>
</head>
<body>
<main class="canvas">
  <section class="card card--front" aria-label="Card front">
    <div class="brand">
      <span class="brand__square"></span>
      <span class="brand__name">Cedar Ridge Mechanical</span>
    </div>
  </section>

  <section class="card card--back" aria-label="Card back">
    <div class="back__brand">
      <div class="brand">
        <span class="brand__square"></span>
        <span class="brand__name">Cedar Ridge Mechanical</span>
      </div>
    </div>
    <div class="divider"></div>
    <div class="contact">
      <h1 class="contact__name">DANIEL HART</h1>
      <p class="contact__role">Managing Director</p>
      <ul class="contact__list">
        <li><svg viewBox="0 0 12 12" aria-hidden="true"><path d="M2.5 1h2l1 3-1.5 1a7 7 0 0 0 3 3l1-1.5 3 1v2a1 1 0 0 1-1 1A10 10 0 0 1 1.5 2a1 1 0 0 1 1-1z"/></svg>123 456 789</li>
        <li><svg viewBox="0 0 12 12" aria-hidden="true"><path d="M1 3h10v7H1z M1 3l5 4 5-4" fill="none" stroke="#0d0d0d" stroke-width="1.2"/></svg>info@yourgmail.com</li>
        <li><svg viewBox="0 0 12 12" aria-hidden="true"><circle cx="6" cy="6" r="5"/></svg>www.yourwebsite.com</li>
      </ul>
    </div>
    <div class="band">Your address, City State, Zip 1234</div>
  </section>
</main>
</body>
</html>
```